Stylish Business Cards Wanted

- DOUBLE SIDED Design Required -

High end, edgy cards for a corporate and personal stylist. Must include logo,
Name: Belinda Harwick
Title: Director and Stylist
telephone : +61 8 7142 5809
email: belinda@theloombriefing.example
website: theloombriefing.example
Tag: Corporate Workwear & Uniform Specialist | Personal Stylist
Would like nice icons for telephone, email, website

Target Market(s)

Businesses wanting stylish uniforms, people wanting stylish wardrobes

Industry/Entity Type

Corporate Workwear Stylist

Contact Information for Business Card

I would like black, white and gold foiling incorporated in the design - possibly a touch of the other colours on my branding guide attached Name: Belinda Harwick Title: Director and Stylist telephone : +61 8 7142 5809 email: belinda@theloombriefing.example website: theloombriefing.example Tag: Corporate Workwear & Uniform Specialist | Personal Stylist Would like nice icons for telephone, email, website

Font styles to use
Other font styles liked:
• Raleway

Colors

Designer to choose colors to be used in the design.

Requirements
Must have
• Gold foil accents

```html
<!DOCTYPE html>
<html lang="en">
<head>
<meta charset="utf-8">
<title>The Loom Briefing – Business Card</title>
<link rel="stylesheet" href="https://fonts.googleapis.com/css2?family=Roboto:wght@400;500&family=Dancing+Script:wght@600&family=Kalam:wght@400&display=swap">
<style>
  :root {
    --backdrop: #d9d8da;
    --card-black: #1c1b1e;
    --pattern-tone-a: #2a292d;
    --pattern-tone-b: #3c3b40;
    --gold: #e2b94f;
    --gold-band: #e7c062;
    --white: #f4f3f1;
    --ink: #1d1c1f;
  }
  * { box-sizing: border-box; margin: 0; padding: 0; }
  html, body { width: 799px; height: 1200px; overflow: hidden; }
  body {
    background: var(--backdrop);
    display: flex;
    align-items: center;
    justify-content: center;
    gap: 40px;
    font-family: "Roboto", Arial, sans-serif;
  }
  .card {
    position: relative;
    width: 350px;
    height: 612px;
    background: var(--card-black);
    overflow: hidden;
  }
  .card-front .tonal-pattern {
    position: absolute;
    inset: 0;
    background: radial-gradient(ellipse at 70% 75%, var(--pattern-tone-b), var(--pattern-tone-a) 55%, var(--card-black) 100%);
  }
  .wordmark {
    font-family: "Roboto", Arial, sans-serif;
    font-weight: 500;
    color: var(--gold);
    text-align: center;
    letter-spacing: 0.04em;
    display: flex;
    align-items: center;
    justify-content: center;
    gap: 10px;
  }
  .wordmark .mark-square {
    width: 12px; height: 12px; background: var(--gold); flex: none;
  }
  .card-front .wordmark {
    position: absolute;
    left: 0; right: 0; top: 50%;
    transform: translateY(-50%);
    font-size: 24px;
  }
  .card-back .wordmark {
    position: absolute;
    left: 0; right: 0; top: 120px;
    font-size: 28px;
  }
  .contact-block {
    position: absolute;
    left: 0; right: 0; top: 240px;
    text-align: center;
    color: var(--white);
  }
  .person-name {
    font-family: "Dancing Script", cursive;
    font-weight: 600;
    font-size: 27px;
    color: var(--gold);
  }
  .person-title { font-size: 14px; margin-top: 2px; }
  .contact-icons {
    display: flex; justify-content: center; gap: 6px; margin-top: 18px;
  }
  .contact-icons svg { width: 16px; height: 16px; }
  .divider {
    width: 150px; height: 2px; margin: 14px auto 18px;
    background: linear-gradient(90deg, transparent, var(--gold), transparent);
  }
  .contact-line { font-size: 15px; line-height: 26px; }
  .tag-band {
    position: absolute;
    left: 0; right: 0; bottom: 0;
    height: 128px;
    background: var(--gold-band);
    display: flex; flex-direction: column; justify-content: center;
    text-align: center;
    font-family: "Kalam", cursive;
    font-size: 16px;
    line-height: 24px;
    color: var(--ink);
  }
  .tag-band .sep { display: inline-block; width: 1px; height: 18px; background: var(--ink); margin: 0 8px; vertical-align: middle; }
</style>
</head>
<body>
  <section class="card card-front">
    <div class="tonal-pattern" role="img" aria-label="Tonal embossed repeat pattern of the brand wordmark on black"></div>
    <div class="wordmark"><span class="mark-square"></span>The Loom Briefing</div>
  </section>

  <section class="card card-back">
    <div class="wordmark">The Loom Briefing</div>
    <div class="contact-block">
      <div class="person-name">Belinda Harwick</div>
      <div class="person-title">Director and Stylist</div>
      <div class="contact-icons">
        <svg viewBox="0 0 16 16" aria-label="Telephone"><circle cx="8" cy="8" r="7" fill="none" stroke="#e2b94f" stroke-width="1.2"/><path d="M5.5 4.5l1.5 1.5-0.8 1.2c.5 1 1.3 1.8 2.3 2.3l1.2-.8 1.5 1.5-1 1c-2.8-.6-5-2.8-5.6-5.6z" fill="#e2b94f"/></svg>
        <svg viewBox="0 0 16 16" aria-label="Email"><circle cx="8" cy="8" r="7" fill="none" stroke="#e2b94f" stroke-width="1.2"/><rect x="4" y="5.2" width="8" height="5.6" fill="none" stroke="#e2b94f" stroke-width="1"/><path d="M4 5.2l4 3 4-3" fill="none" stroke="#e2b94f" stroke-width="1"/></svg>
        <svg viewBox="0 0 16 16" aria-label="Website"><circle cx="8" cy="8" r="7" fill="none" stroke="#e2b94f" stroke-width="1.2"/><circle cx="8" cy="8" r="4.2" fill="none" stroke="#e2b94f" stroke-width="0.9"/><ellipse cx="8" cy="8" rx="1.8" ry="4.2" fill="none" stroke="#e2b94f" stroke-width="0.9"/><path d="M3.8 8h8.4" stroke="#e2b94f" stroke-width="0.9"/></svg>
      </div>
      <div class="divider"></div>
      <div class="contact-line">+61 8 7142 5809</div>
      <div class="contact-line">belinda@theloombriefing.example</div>
      <div class="contact-line">www.theloombriefing.example</div>
    </div>
    <div class="tag-band">
      <div>Corporate Workwear &amp; Uniform</div>
      <div>Specialist<span class="sep"></span>Personal Stylist</div>
    </div>
  </section>
</body>
</html>
```